Brightway Carpet and Tile cleaning Business card Design

I need a design that has the same feel as my van.
i would also like a prominent "Review us on facebook" somewhere, but not that it makes it look silly.
I would like the card to have a little bit of grey or black in the design as well.

It will need contact details
phone: 0455 817264
email: rkbrightwayclean@mailbox-example.com
website: www.brightwaycarpetandtilecleaning-example.com.au
facebook: /brightwaycarpetandtilecleaning

Industry/Entity Type

Business

Contact Information for Business Card

Phone number 0455817264
Email rkbrightwayclean@mailbox-example.com
Website www.brightwaycarpetandtilecleaning-example.com.au
Facebook/brightwaycarpetandtilecleaning

Colors
000000

Requirements
Must have
• Same feel as my van
• I want the card to stand out from the crowd
Nice to have
• Maybe include a tiny bit of a third colour? Grey's,blacks, orange?

```html
<!DOCTYPE html>
<html lang="en">
<head>
<meta charset="utf-8">
<title>Brightway Carpet &amp; Tile Cleaning – Business Card</title>
<link rel="stylesheet" href="https://fonts.googleapis.com/css2?family=Arimo:wght@400;700&display=swap">
<style>
  :root {
    --page-bg: #e9e7e4;
    --card-light: #f4f5f6;
    --card-mid: #e3e6e8;
    --charcoal: #2f3031;
    --green: #6aab45;
    --green-text: #55a434;
    --ink: #1b1b1b;
    --icon-bg: #6aab45;
  }
  * { margin: 0; padding: 0; box-sizing: border-box; }
  html, body {
    width: 1200px; height: 970px; overflow: hidden;
    background: var(--page-bg);
    font-family: "Arimo", Arial, sans-serif;
  }
  .card {
    position: absolute; left: 50px; top: 172px;
    width: 1100px; height: 626px;
    background: linear-gradient(160deg, var(--card-light) 0%, var(--card-mid) 100%);
    box-shadow: 0 10px 30px rgba(0,0,0,.18);
    overflow: hidden;
  }
  .card-shapes { position: absolute; inset: 0; width: 100%; height: 100%; }
  .brand {
    position: absolute; left: 430px; top: 150px;
    display: flex; align-items: center; gap: 16px;
    color: var(--green-text); font-weight: 700;
  }
  .brand-dot { width: 34px; height: 34px; border-radius: 50%; background: var(--green-text); flex: none; }
  .brand-name { font-size: 62px; line-height: 1; }
  .brand-line { font-size: 22px; letter-spacing: 2px; margin-top: 6px; }
  .person {
    position: absolute; right: 50px; top: 312px; text-align: right;
  }
  .person-name { font-size: 33px; font-weight: 700; color: var(--ink); }
  .person-role { font-size: 26px; color: var(--green-text); margin-top: 2px; }
  .contacts {
    position: absolute; right: 50px; top: 410px;
    list-style: none; text-align: right;
  }
  .contacts li {
    display: flex; justify-content: flex-end; align-items: center; gap: 12px;
    font-size: 26px; color: var(--ink); height: 39px;
  }
  .icon {
    width: 30px; height: 30px; background: var(--icon-bg);
    display: inline-flex; align-items: center; justify-content: center; flex: none;
  }
  .icon svg { width: 20px; height: 20px; }
</style>
</head>
<body>
  <div class="card">
    <svg class="card-shapes" viewBox="0 0 1040 592" preserveAspectRatio="none" aria-hidden="true">
      <path d="M0,0 L95,0 A720,720 0 0,0 400,592 L0,592 Z" fill="var(--charcoal)"/>
      <circle cx="820" cy="20" r="712" fill="none" stroke="#ffffff" stroke-width="8"/>
      <circle cx="820" cy="20" r="694" fill="none" stroke="var(--green)" stroke-width="16"/>
      <path d="M880,592 Q970,565 1040,520 L1040,592 Z" fill="var(--charcoal)"/>
      <path d="M860,592 Q960,560 1040,508" fill="none" stroke="var(--green)" stroke-width="6"/>
    </svg>

    <div class="brand">
      <span class="brand-dot"></span>
      <div>
        <div class="brand-name">Brightway</div>
        <div class="brand-line">CARPET &amp; TILE CLEANING</div>
      </div>
    </div>

    <div class="person">
      <div class="person-name">Marco Bellini</div>
      <div class="person-role">Managing/Director</div>
    </div>

    <ul class="contacts">
      <li>0455 817264
        <span class="icon"><svg viewBox="0 0 20 20"><path d="M5 2 L8 2 L9 6 L7 8 Q9 12 12 13 L14 11 L18 12 L18 15 Q17 18 14 18 Q3 16 2 5 Q2 2 5 2 Z" fill="#fff"/></svg></span>
      </li>
      <li>rkbrightwayclean@mailbox-example.com
        <span class="icon"><svg viewBox="0 0 20 20"><rect x="2" y="4" width="16" height="12" fill="none" stroke="#fff" stroke-width="1.6"/><path d="M2 4 L10 11 L18 4" fill="none" stroke="#fff" stroke-width="1.6"/></svg></span>
      </li>
      <li>www.brightwaycarpetandtilecleaning-example.com.au
        <span class="icon"><svg viewBox="0 0 20 20"><circle cx="10" cy="10" r="7.5" fill="none" stroke="#fff" stroke-width="1.5"/><ellipse cx="10" cy="10" rx="3.5" ry="7.5" fill="none" stroke="#fff" stroke-width="1.3"/><path d="M2.5 10 H17.5 M4 6 H16 M4 14 H16" stroke="#fff" stroke-width="1.2"/></svg></span>
      </li>
      <li>/brightwaycarpetandtilecleaning
        <span class="icon"></span>
      </li>
    </ul>
  </div>
</body>
</html>
```